Quillbay.vc needs a better website design!

We need a new and better website for Quillbay.vc. We're a Canadian venture capital firm that invests in innovative entrepreneurs. We compete against the following websites: tormelo.vc, brightvalefund.ca, kestrowvc.com, and dovaran.vc. We're a diverse group of partners and we're dedicated to the founders we invest in.
Updates

I don’t really like stock photos of random people as part of the website design…so please try to stay away from using those images. Thanks, Owen

Target Market(s)

Canadian entrepreneurs and investors

Industry/Entity Type

Venture capital, finance, investment, entrepreneurship

Coding

Coded - Design and coding required

Number of Pages Required

4 page

Font styles to use
Sans Serif

Colors

Designer to choose colors to be used in the design.

Requirements
Must have
• Clean crisp overall design. Fast and to the point.
Nice to have
• Check out www.quillbay.vc - I did it myself and it is too basic and too wordy.
Should not have
• No stock images with random people in them! Not too wordy or with too many large images that are slow to load.

```html
<!DOCTYPE html>
<html lang="en">
<head>
<meta charset="utf-8">
<title>Quillbay.vc — Venture Capital</title>
<link href="https://fonts.googleapis.com/css2?family=Poppins:wght@400;500;600;700&display=swap" rel="stylesheet">
<style>
:root{
  --green:#7f9b2e;
  --green-mid:#9cb45a;
  --green-soft:#bfd08c;
  --panel:#eef2d8;
  --panel-line:#dfe7bd;
  --ink:#333333;
  --ink-soft:#555555;
  --white:#ffffff;
  --footer-bg:#f6f6f6;
  --tile-border:#ececec;
}
*{margin:0;padding:0;box-sizing:border-box}
html,body{width:1200px;height:2299px;overflow:hidden}
body{position:relative;font-family:'Poppins',sans-serif;color:var(--ink);background:var(--white)}
.abs{position:absolute}

/* header */
.site-header{position:absolute;left:0;top:0;width:1200px;height:96px;background:var(--white);border-bottom:1px solid #e2e2e2}
.brand{position:absolute;left:162px;top:22px;display:flex;align-items:center;gap:8px}
.brand-dot{width:14px;height:14px;border-radius:50%;background:var(--green)}
.brand-name{font-weight:600;font-size:17px;color:var(--green);letter-spacing:.5px}
.nav a{position:absolute;top:38px;font-size:14px;color:var(--ink-soft);text-decoration:none}
.nav .active-tab{position:absolute;left:705px;top:0;width:64px;height:101px;background:#f3f3f3;border-bottom:4px solid var(--green)}
.nav .active{color:var(--green);font-weight:500}

/* hero */
.hero{position:absolute;left:0;top:96px;width:1200px;height:545px;
  background:linear-gradient(180deg,#7f98ad 0%,#8e9a92 22%,#4d5e3b 45%,#34442a 70%,#5b5a52 100%)}
.hero-title{position:absolute;left:80px;top:148px;width:1040px;text-align:center;color:var(--white);font-size:30px;line-height:51px;font-weight:400}
.numbers-label{position:absolute;left:0;top:325px;width:1200px;text-align:center;color:var(--white);font-size:19px;font-weight:500}
.numbers-rule{position:absolute;top:338px;height:1px;width:210px;background:rgba(255,255,255,.45)}
.stat-caption{color:var(--white);font-size:15px;line-height:18px}
.stat-num{color:var(--green-mid);font-weight:500;font-size:38px}
.stat-dot{width:7px;height:7px;border-radius:50%;background:var(--white)}
.hero-ring{position:absolute;left:431px;top:430px;width:324px;height:324px;border-radius:50%;background:rgba(255,255,255,.06)}
.hero-badge{position:absolute;left:493px;top:490px;width:200px;height:200px;border-radius:50%;border:6px solid var(--white)}

/* intro */
.intro{position:absolute;left:0;top:710px;width:1200px;text-align:center;font-size:26px;line-height:37px;color:var(--ink-soft)}

.service-text{position:absolute;font-size:15px;line-height:25px;color:var(--ink)}

/* portfolio */
.section-title{position:absolute;left:0;width:1200px;text-align:center;font-size:26px;color:var(--ink-soft)}
.tile{position:absolute;width:154px;height:67px;background:var(--white);border:1px solid var(--tile-border);box-shadow:0 2px 6px rgba(0,0,0,.06);
  display:flex;align-items:center;justify-content:center;font-size:18px;font-weight:600;color:#2b2b2b}

/* cta */
.cta{position:absolute;left:0;top:1515px;width:1200px;height:450px;
  background:linear-gradient(180deg,#3e4a3a 0%,#34422f 50%,#1f2a1d 100%)}
.cta-title{position:absolute;left:0;top:1672px;width:1200px;text-align:center;color:var(--white);font-size:50px;line-height:63px;font-weight:500}
.cta-link{position:absolute;left:0;top:1828px;width:1200px;text-align:center;color:var(--green-mid);font-size:27px;font-weight:500}

/* footer */
.site-footer{position:absolute;left:0;top:1965px;width:1200px;height:270px;background:var(--footer-bg)}
.foot-head{position:absolute;font-size:20px;font-weight:500;color:var(--ink)}
.foot-link{position:absolute;left:162px;font-size:14px;color:var(--ink-soft)}
.foot-link::before{content:"›";margin-right:9px}
.foot-text{position:absolute;font-size:14px;color:var(--ink-soft)}
.social{position:absolute;top:2143px;width:30px;height:30px;border-radius:50%}
.foot-brand{position:absolute;left:875px;top:2070px;display:flex;align-items:center;gap:10px}
.foot-brand .brand-dot{width:22px;height:22px}
.foot-brand .brand-name{font-size:28px;font-weight:600}
.copyright{position:absolute;left:0;top:2235px;width:1200px;height:64px;background:var(--green);color:var(--white);font-size:14px;font-weight:500;text-align:center;line-height:54px}
</style>
</head>
<body>

<header class="site-header">
  <div class="brand"><span class="brand-dot"></span><span class="brand-name">QUILLBAY.VC</span></div>
  <nav class="nav">
    <span class="active-tab"></span>
    <a class="active" style="left:717px">Home</a>
    <a style="left:809px">What</a>
    <a style="left:896px">Who</a>
    <a style="left:978px">Portfolio</a>
  </nav>
</header>

<section class="hero" role="img" aria-label="Mountain valley with a forest-lined road and a red car"></section>
<p class="hero-title">Quillbay.vc is a venture capital firm that invests in innovative seed-stage technology companies in Western Canada focused on B2B and SaaS markets.</p>
<div class="numbers-rule" style="left:262px"></div>
<div class="numbers-rule" style="left:723px"></div>
<p class="numbers-label">Quillbay.vc in numbers</p>
<div class="hero-ring"></div>
<div class="hero-badge"></div>
<p class="abs stat-caption" style="left:0;top:369px;width:1200px;text-align:center">Follow-on financings</p>
<p class="abs stat-num" style="left:0;top:403px;width:1178px;text-align:center">07</p>
<span class="abs stat-dot" style="left:589px;top:455px"></span>
<p class="abs stat-caption" style="left:300px;top:545px;width:101px;text-align:right">Portfolio companies</p>
<p class="abs stat-num" style="left:412px;top:538px">10</p>
<span class="abs stat-dot" style="left:462px;top:560px"></span>
<span class="abs stat-dot" style="left:716px;top:560px"></span>
<p class="abs stat-num" style="left:733px;top:538px">100</p>
<p class="abs stat-caption" style="left:802px;top:546px">+<br>Employees</p>

<p class="intro">We are serial entrepreneurs and venture<br>capital investors who provide</p>

<svg class="abs" style="left:160px;top:826px" width="880" height="274" viewBox="0 0 880 274" aria-hidden="true">
  <path d="M20 2 H357 Q366 2 371 10 L442 132 L512 10 Q517 2 526 2 H858 Q878 2 878 22 V250 Q878 270 858 270 H526 Q517 270 512 262 L442 140 L371 262 Q366 270 357 270 H20 Q2 270 2 250 V22 Q2 2 20 2 Z" fill="var(--panel)" stroke="var(--panel-line)"/>
  <circle cx="439" cy="134" r="78" fill="var(--green-soft)"/>
  <circle cx="439" cy="134" r="59" fill="var(--green-mid)"/>
  <circle cx="439" cy="134" r="36" fill="none" stroke="var(--white)" stroke-width="4"/>
  <g fill="none" stroke="var(--green-mid)" stroke-width="3">
    <rect x="38" y="108" width="13" height="18"/><rect x="58" y="96" width="13" height="30"/>
    <rect x="78" y="82" width="13" height="44"/><rect x="98" y="66" width="13" height="60"/>
  </g>
  <path d="M40 60 Q75 58 90 38" fill="none" stroke="var(--green)" stroke-width="3"/>
  <path d="M82 36 L92 34 L91 44" fill="none" stroke="var(--green)" stroke-width="3"/>
  <circle cx="813" cy="104" r="19" fill="none" stroke="var(--green)" stroke-width="2.5"/>
  <text x="813" y="112" text-anchor="middle" font-family="Poppins,sans-serif" font-size="22" fill="var(--green)">$</text>
</svg>
<p class="service-text" style="left:196px;top:969px">Mentoring and strategic advice<br>to help you grow your company quickly<br>and efficiently</p>
<p class="service-text" style="left:700px;top:969px;width:292px;text-align:right">Investor introductions to help you raise additional follow-on funding for your startup</p>

<h2 class="section-title" style="top:1184px">Check out our innovative portfolio companies!</h2>
<div class="tile" style="left:162px;top:1258px">Lumen Tally</div>
<div class="tile" style="left:342px;top:1258px">fairwind</div>
<div class="tile" style="left:523px;top:1258px">Soundkeel</div>
<div class="tile" style="left:704px;top:1258px">Trelloq</div>
<div class="tile" style="left:884px;top:1258px">Norvik</div>
<div class="tile" style="left:162px;top:1346px">Pennaro</div>
<div class="tile" style="left:342px;top:1346px">Crestly</div>
<div class="tile" style="left:523px;top:1346px">Gatewise</div>
<div class="tile" style="left:704px;top:1346px">Homeward</div>
<div class="tile" style="left:884px;top:1346px">Brellix</div>

<section class="cta" role="img" aria-label="Misty green mountain range under a dark sky"></section>
<h2 class="cta-title">If you have what we’re<br>looking for</h2>
<p class="cta-link">Contact us today</p>

<footer class="site-footer"></footer>
<h3 class="foot-head" style="left:162px;top:2019px">Quick Links</h3>
<p class="foot-link" style="top:2060px">Home</p>
<p class="foot-link" style="top:2093px">What</p>
<p class="foot-link" style="top:2125px">Who</p>
<p class="foot-link" style="top:2157px">Portfolio</p>
<h3 class="foot-head" style="left:424px;top:2019px">Get In Touch</h3>
<p class="foot-text" style="left:424px;top:2060px"><b style="font-weight:600">Email:</b>&nbsp; info@quillbay.vc</p>
<h3 class="foot-head" style="left:424px;top:2104px">Follow Us</h3>
<span class="social" style="left:425px;background:#3fa9e8" aria-label="Chirpline profile"></span>
<span class="social" style="left:462px;background:#1b7fb5" aria-label="Workwire profile"></span>
<div class="foot-brand"><span class="brand-dot"></span><span class="brand-name">QUILLBAY.VC</span></div>
<div class="copyright">Copyright © 2021 Quillbay.vc - All Rights Reserved.</div>

</body>
</html>
```